Kestrel Facilities Business Card Design

We would now like to design business cards with the new Kestrel Facilities logo

Target Market(s)

Professional

Industry/Entity Type

Professional services

Contact Information for Business Card

Employee name, title, phone number, email address, corporate office address and logo.

Font styles to use
Sans Serif

Colors
0054AA
0677BA
7BADD7
CADEEF
E8F1F8

Requirements
Must have
• My logo
Should not have
• any other pictures or images besides my logo

```html
<!DOCTYPE html>
<html lang="en">
<head>
<meta charset="utf-8">
<title>Kestrel Facilities – Business Card</title>
<link href="https://fonts.googleapis.com/css2?family=Oswald:wght@500;600&family=Arimo:wght@400;700&display=swap" rel="stylesheet">
<style>
  :root{
    --blue-deep:#0054AA;
    --blue:#0677BA;
    --blue-bright:#0a7fe0;
    --blue-soft:#7BADD7;
    --blue-pale:#CADEEF;
    --blue-mist:#E8F1F8;
    --ink:#111;
    --paper:#fff;
    --stage:#2b2b2b;
  }
  *{box-sizing:border-box;margin:0;padding:0}
  html,body{width:1200px;height:866px;overflow:hidden;background:var(--stage)}
  .stage{width:1200px;height:866px;display:flex;align-items:center;justify-content:center;gap:40px}
  .card{width:540px;height:309px;position:relative;overflow:hidden;box-shadow:0 10px 30px rgba(0,0,0,.5)}
  .card-front{background:var(--paper);font-family:"Arimo",sans-serif;color:var(--ink)}
  .holder{position:absolute;left:34px;top:92px}
  .holder-name{font-family:"Oswald",sans-serif;font-weight:600;font-size:24px;color:var(--blue-bright);letter-spacing:.3px;text-transform:uppercase;line-height:1}
  .holder-title{font-size:14px;margin-top:4px}
  .divider{position:absolute;left:34px;right:34px;top:146px;height:1px;background:var(--blue-bright)}
  .contacts{position:absolute;left:34px;top:156px}
  .contact{font-size:13px;line-height:19px;display:flex;align-items:center;gap:7px}
  .contact svg{width:13px;height:13px;flex:none}
  .brand{position:absolute;right:34px;top:92px;display:flex;align-items:center;gap:10px}
  .brand-mark{width:22px;height:22px;background:var(--blue-bright)}
  .brand-name{font-family:"Oswald",sans-serif;font-weight:600;font-size:30px;color:var(--blue-bright);line-height:1}
  .address{position:absolute;right:34px;top:158px;text-align:right;font-size:13px;line-height:19px}
  .base{position:absolute;left:0;bottom:0;width:540px;height:60px}
  .website{position:absolute;right:34px;bottom:10px;color:var(--paper);font-size:13px;letter-spacing:.3px}
  .card-back{background:var(--blue-bright);display:flex;align-items:center;justify-content:center}
  .back-field{position:absolute;inset:0;background:radial-gradient(ellipse at 60% 40%,#2e95ec 0%,var(--blue-bright) 55%,#0668c4 100%)}
  .card-back .brand{position:relative;right:auto;top:auto;gap:14px}
  .card-back .brand-mark{width:30px;height:30px;background:var(--paper)}
  .card-back .brand-name{color:var(--paper);font-size:40px}
</style>
</head>
<body>
<main class="stage">
  <section class="card card-front" aria-label="Business card front">
    <div class="holder">
      <p class="holder-name">Daniel Harper</p>
      <p class="holder-title">Managing Director</p>
    </div>
    <div class="brand">
      <span class="brand-mark"></span>
      <span class="brand-name">Kestrel Facilities</span>
    </div>
    <div class="divider"></div>
    <div class="contacts">
      <p class="contact">
        <svg viewBox="0 0 16 16"><path d="M4 1l3 3-1.5 2a8 8 0 0 0 4.5 4.5L12 9l3 3-2 2.5C7 14 2 9 1.5 3z" fill="var(--blue-bright)"/></svg>
        044-555 210 734
      </p>
      <p class="contact">
        <svg viewBox="0 0 16 16"><rect x="1" y="3" width="14" height="10" fill="var(--blue-bright)"/><path d="M1 3l7 6 7-6" stroke="#fff" stroke-width="1.3" fill="none"/></svg>
        info@kestrelfac.com
      </p>
    </div>
    <p class="address">18 Harbour Row, Suite 4<br>20817, Northvale</p>
    <svg class="base" viewBox="0 0 540 60" preserveAspectRatio="none">
      <path d="M0 44 L230 44 C244 44 246 32 262 32 L540 32 L540 60 L0 60 Z" fill="var(--blue-bright)"/>
      <path d="M0 38 L226 38" stroke="var(--blue-bright)" stroke-width="2"/>
    </svg>
    <p class="website">www.kestrelfac.com</p>
  </section>

  <section class="card card-back" aria-label="Business card back">
    <div class="back-field" role="img" aria-label="Soft blue background where the large faint brand decoration sits"></div>
    <div class="brand">
      <span class="brand-mark"></span>
      <span class="brand-name">Kestrel Facilities</span>
    </div>
  </section>
</main>
</body>
</html>
```